Website Development for vaultmerrow.com.au

Build a new Wordpress/Responsive website for vaultmerrow.com.au

Target Market(s)

Compliance Managers, Risk Managers, Information Security and Cyber Security Professionals, Chief Data/Digital Officers, Chief Operating/Financial Officers, Business Continuity Professionals, Disaster Recovery Planners, Small Business Owners, Local/Federal Government entities

Industry/Entity Type

Data Service

Coding

Coded - Design and coding required

Number of Pages Required

5+ page

Font styles to use
Sans Serif

Colors

Designer to choose colors to be used in the design.

Requirements
Must have
• 1. Site Structure: Home Page plus the following chapter-pages for a) Services b) About c) Resources d) Blog e) Contact Us
• 2. Prefer site to built on wordpress and we can purchase a theme if needed (we currently use Kelp9 for other sites)
• 3. Blog needs to be wordpress based
• 4. We will host the site ourselves on our own servers
• 5. Responsive Design
Nice to have
• 1. Livechat capability/interface
• 2. Capability for marketing automation integration (such as hubspot, marketo, infusionsoft etc)
• 3. Capability for CRM integration (Salesforce)

```html
<!DOCTYPE html>
<html lang="en">
<head>
<meta charset="utf-8">
<title>Vaultmerrow — Data Resilience</title>
<link rel="stylesheet" href="https://fonts.googleapis.com/css2?family=Roboto:wght@400;500;700;900&display=swap">
<style>
:root{
  --red:#e30613;
  --red-dark:#c10510;
  --red-soft:#fbd3d6;
  --ink:#1c1c1c;
  --grey:#6f6f6f;
  --line:#e2e2e2;
  --paper:#ffffff;
  --navy:#16213a;
}
*{box-sizing:border-box;margin:0;padding:0}
html,body{width:1200px;height:4080px;overflow:hidden;background:var(--paper)}
body{font-family:'Roboto',Arial,sans-serif;color:var(--ink)}
.page{position:relative;width:1200px;height:4080px;overflow:hidden}
.abs{position:absolute}
.brand{left:118px;top:14px;display:flex;align-items:center;gap:10px}
.brand-mark{width:30px;height:30px;background:var(--red);border-radius:50%}
.brand-name{font-size:34px;font-weight:900;color:var(--red);letter-spacing:-.5px}
.main-nav{right:28px;top:38px;display:flex;gap:46px;z-index:3}
.main-nav a{font-size:17px;font-weight:700;color:var(--ink);text-decoration:none}
.hero-art{left:470px;top:0;width:730px;height:560px;border-bottom-left-radius:60% 80%;
  background:radial-gradient(circle at 62% 45%,#e30613 0 12%,#f37c84 22%,#fbd3d6 45%,#fff 75%)}
.section-no{left:24px;font-size:22px;font-weight:700;color:var(--red)}
.side-dots{left:36px;display:flex;flex-direction:column;gap:18px}
.side-dots span{width:8px;height:8px;border-radius:50%;background:#cfcfcf}
.side-dots span.on{background:var(--red)}
.side-dots em{position:absolute;left:14px;font-style:normal;font-size:9px;color:var(--red)}
.hero-title{left:108px;top:275px;font-size:58px;font-weight:700}
.hero-lead{left:108px;top:350px;font-size:21px;line-height:28px;color:var(--ink)}
.btn{display:inline-flex;align-items:center;justify-content:center;background:var(--red);color:#fff;
  font-weight:700;border-radius:30px;text-decoration:none;box-shadow:0 6px 14px rgba(227,6,19,.3)}
.hero-btn{left:108px;top:458px;width:214px;height:54px;font-size:18px}
.scroll-mouse{left:588px;top:566px}
.section-title{left:0;width:1200px;text-align:center;font-size:50px;font-weight:500}
.section-icon{left:578px}
.card{position:absolute;width:320px;height:330px;border:1px solid var(--line);background:#fff;text-align:center;padding:140px 26px 0}
.card.active{border:2px solid var(--red)}
.card-icon{position:absolute;left:50%;top:-40px;transform:translateX(-50%);width:138px;height:138px;border-radius:50%;
  background:#fff;border:1px solid var(--line);display:flex;align-items:center;justify-content:center}
.card-icon i{width:108px;height:108px;border-radius:50%;background:#f2f2f2;display:flex;align-items:center;justify-content:center}
.card.active .card-icon i{background:var(--red)}
.card h3{font-size:22px;font-weight:500;margin-bottom:28px}
.card p{font-size:14px;line-height:22px;color:var(--grey)}
.about-band{left:0;top:1760px;width:1200px;height:660px}
.about-photo{left:108px;top:1985px;width:455px;height:345px;background:linear-gradient(135deg,#0d1a33,#2a3f6b 55%,#4b6a9c)}
.about-title{left:600px;top:1845px;font-size:50px;font-weight:500}
.about-lead{left:600px;top:1935px;width:520px;font-size:15px;line-height:23px;color:var(--red);font-weight:500}
.tick-list{left:600px;top:2010px;width:520px;list-style:none}
.tick-list li{display:flex;gap:14px;font-size:14px;line-height:22px;color:var(--grey);margin-bottom:18px}
.tick-list svg{flex:none;margin-top:2px}
.about-btn{left:600px;top:2180px;width:176px;height:48px;font-size:15px}
.resources-text{left:170px;top:2530px;width:860px;text-align:center;font-size:17px;line-height:28px;color:var(--grey)}
.res-btn{left:512px;top:2690px;width:176px;height:50px;font-size:15px}
.post{position:absolute;top:3040px;width:300px;height:420px;background:#fff;box-shadow:0 4px 18px rgba(0,0,0,.12)}
.post-img{height:210px}
.post p{font-size:15px;line-height:23px;color:var(--grey);padding:24px 22px 0}
.post-meta{position:absolute;left:22px;bottom:30px;right:22px;display:flex;align-items:center;justify-content:space-between}
.author{display:flex;align-items:center;gap:10px;font-size:13px;font-weight:700}
.author i{width:40px;height:40px;border-radius:50%;background:#c9b8aa}
.post .btn{width:104px;height:36px;font-size:12px}
.footer-brand{left:118px;top:3545px}
.foot-title{font-size:26px;font-weight:500;margin-bottom:30px}
.foot-col{top:3715px}
.foot-col dt{font-size:14px;font-weight:700;margin-top:12px}
.foot-col dd{font-size:13px;color:var(--grey);margin-bottom:16px}
.socials{display:flex;gap:12px;margin-top:10px}
.socials span{width:22px;height:22px;background:var(--red);border-radius:3px}
.links{list-style:none}
.links li{font-size:14px;color:var(--grey);line-height:24px}
.newsletter{left:670px;top:3700px;width:480px;color:#fff}
.newsletter h3{font-size:30px;font-weight:500;margin-bottom:26px}
.newsletter p{font-size:15px;line-height:23px;margin-bottom:36px}
.signup{display:flex;align-items:center;justify-content:space-between;width:460px;height:52px;border:1px solid #fff;border-radius:30px;padding:0 6px 0 26px}
.signup span{font-size:13px;color:#ffd9dc}
.signup b{background:#fff;color:var(--red);border-radius:24px;padding:12px 28px;font-size:16px}
.copyright{left:730px;top:4040px;font-size:13px;color:#fff}
</style>
</head>
<body>
<div class="page">

  <!-- Header -->
  <div class="abs hero-art" role="img" aria-label="Red digital security artwork with a padlock over circuit lines"></div>
  <div class="abs brand"><span class="brand-mark"></span><span class="brand-name">Vaultmerrow</span></div>
  <nav class="abs main-nav"><a href="#">SERVICES</a><a href="#">ABOUT</a><a href="#">RESOURCES</a><a href="#">BLOG</a><a href="#">CONTACT US</a></nav>

  <!-- Hero -->
  <div class="abs section-no" style="top:325px">01</div>
  <div class="abs side-dots" style="top:365px"><span class="on"></span><span></span><span></span><span></span><span></span></div>
  <h1 class="abs hero-title">Data Resilience</h1>
  <p class="abs hero-lead">Lorem ipsum dolor sit amet, consectetur<br>adipiscing elit, sed do eiusmod</p>
  <a class="abs btn hero-btn" href="#">Get Started</a>
  <svg class="abs scroll-mouse" width="24" height="40" viewBox="0 0 24 40"><rect x="2" y="2" width="20" height="34" rx="10" fill="none" stroke="#333" stroke-width="2"/><line x1="12" y1="9" x2="12" y2="15" stroke="#333" stroke-width="2"/></svg>

  <!-- Services -->
  <h2 class="abs section-title" style="top:725px">Our Services</h2>
  <svg class="abs section-icon" style="top:800px" width="44" height="40" viewBox="0 0 44 40"><circle cx="16" cy="22" r="9" fill="none" stroke="#777" stroke-width="4" stroke-dasharray="4 3"/><circle cx="16" cy="22" r="4" fill="#777"/><circle cx="33" cy="11" r="6" fill="none" stroke="#999" stroke-width="3" stroke-dasharray="3 2"/></svg>

  <div class="abs section-no" style="top:1262px">02</div>
  <div class="abs side-dots" style="top:1300px"><span></span><span class="on"></span><span></span><span></span><span></span><span></span></div>

  <div class="card" style="left:100px;top:985px">
    <div class="card-icon"><i><svg width="48" height="44" viewBox="0 0 48 44"><path d="M24 3 45 41H3Z" fill="var(--red)"/><rect x="22" y="16" width="4" height="13" fill="#fff"/><rect x="22" y="32" width="4" height="4" fill="#fff"/></svg></i></div>
    <h3>RISK MANAGEMENT</h3>
    <p>Lorem ipsum dolor sit amet, consectetur adipiscing elit, sed do eiusmod tempor incididunt ut labore et dolore magna aliqua. Ut enim ad minim veniam, quis nostrud exercitation ullamco laboris nisi ut aliquip.</p>
  </div>
  <div class="card active" style="left:440px;top:985px">
    <div class="card-icon"><i><svg width="50" height="50" viewBox="0 0 50 50"><circle cx="25" cy="25" r="21" fill="none" stroke="#fff" stroke-width="3"/><ellipse cx="25" cy="25" rx="9" ry="21" fill="none" stroke="#fff" stroke-width="3"/><line x1="4" y1="25" x2="46" y2="25" stroke="#fff" stroke-width="3"/><rect x="27" y="28" width="16" height="13" rx="2" fill="#fff"/></svg></i></div>
    <h3>CYBER SECURITY</h3>
    <p>Lorem ipsum dolor sit amet, consectetur adipiscing elit, sed do eiusmod tempor incididunt ut labore et dolore magna aliqua. Ut enim ad minim veniam, quis nostrud exercitation ullamco laboris nisi ut aliquip.</p>
  </div>
  <div class="card" style="left:780px;top:985px">
    <div class="card-icon"><i><svg width="48" height="48" viewBox="0 0 48 48"><path d="M24 4 40 10V24C40 34 32 41 24 44 16 41 8 34 8 24V10Z" fill="var(--red)"/><circle cx="24" cy="24" r="7" fill="none" stroke="#fff" stroke-width="3"/></svg></i></div>
    <h3>INFORMATION SECURITY</h3>
    <p>Lorem ipsum dolor sit amet, consectetur adipiscing elit, sed do eiusmod tempor incididunt ut labore et dolore magna aliqua. Ut enim ad minim veniam, quis nostrud exercitation ullamco laboris nisi ut aliquip.</p>
  </div>

  <div class="card" style="left:100px;top:1390px">
    <div class="card-icon"><i><svg width="52" height="40" viewBox="0 0 52 40"><path d="M14 36H40A10 10 0 0 0 38 16 14 14 0 0 0 12 18 9 9 0 0 0 14 36Z" fill="var(--red)"/><path d="M26 14V30M20 24 26 30 32 24" stroke="#fff" stroke-width="3" fill="none"/></svg></i></div>
    <h3>DISASTER RECOVERY</h3>
    <p>Lorem ipsum dolor sit amet, consectetur adipiscing elit, sed do eiusmod tempor incididunt ut labore et dolore magna aliqua. Ut enim ad minim veniam, quis nostrud exercitation ullamco laboris nisi ut aliquip.</p>
  </div>
  <div class="card" style="left:440px;top:1390px">
    <div class="card-icon"><i><svg width="48" height="48" viewBox="0 0 48 48"><path d="M24 4 40 10V24C40 34 32 41 24 44 16 41 8 34 8 24V10Z" fill="var(--red)"/><path d="M16 24 22 30 33 18" stroke="#fff" stroke-width="4" fill="none"/></svg></i></div>
    <h3>COMPLIANCE MANAGEMENT</h3>
    <p>Lorem ipsum dolor sit amet, consectetur adipiscing elit, sed do eiusmod tempor incididunt ut labore et dolore magna aliqua. Ut enim ad minim veniam, quis nostrud exercitation ullamco laboris nisi ut aliquip.</p>
  </div>
  <div class="card" style="left:780px;top:1390px">
    <div class="card-icon"><i><svg width="48" height="48" viewBox="0 0 48 48"><rect x="6" y="8" width="26" height="22" rx="2" fill="var(--red)"/><circle cx="30" cy="28" r="10" fill="none" stroke="#333" stroke-width="4"/><line x1="37" y1="35" x2="45" y2="43" stroke="#333" stroke-width="5"/></svg></i></div>
    <h3>DATA SECURITY</h3>
    <p>Lorem ipsum dolor sit amet, consectetur adipiscing elit, sed do eiusmod tempor incididunt ut labore et dolore magna aliqua. Ut enim ad minim veniam, quis nostrud exercitation ullamco laboris nisi ut aliquip.</p>
  </div>

  <!-- About -->
  <svg class="abs about-band" viewBox="0 0 1200 660" preserveAspectRatio="none"><path d="M0 0C140 40 230 160 300 330 360 480 250 600 0 660Z" fill="var(--red)"/></svg>
  <div class="abs side-dots" style="top:1990px"><span></span><span></span><span class="on"></span><span></span><span></span><span></span></div>
  <div class="abs about-photo" role="img" aria-label="Engineer holding a tablet in a server room"></div>
  <h2 class="abs about-title">About Us</h2>
  <p class="abs about-lead">Lorem ipsum dolor sit amet, consectetur adipiscing elit, sed do eiusmod tempor incididunt ut labore et dolore magna aliqua.</p>
  <ul class="abs tick-list">
    <li><svg width="20" height="20" viewBox="0 0 20 20"><circle cx="10" cy="10" r="9" fill="none" stroke="var(--red)" stroke-width="1.5"/><path d="M5.5 10 8.5 13 14.5 7" stroke="var(--red)" stroke-width="2" fill="none"/></svg>Lorem ipsum dolor sit amet, consectetur adipiscing elit, sed do eiusmod tempor incididunt ut labore et</li>
    <li><svg width="20" height="20" viewBox="0 0 20 20"><circle cx="10" cy="10" r="9" fill="none" stroke="var(--red)" stroke-width="1.5"/><path d="M5.5 10 8.5 13 14.5 7" stroke="var(--red)" stroke-width="2" fill="none"/></svg>Sed ut perspiciatis unde omnis iste natus error sit voluptatem accusantium doloremque laudantium, totam rem aperiam, eaque ipsa quae ab illo inventore veritatis et quasi architecto beatae vitae dicta sunt explicabo.</li>
  </ul>
  <a class="abs btn about-btn" href="#">READ MORE</a>

  <!-- Resources -->
  <h2 class="abs section-title" style="top:2395px">Resources</h2>
  <svg class="abs section-icon" style="top:2470px" width="40" height="40" viewBox="0 0 40 40"><ellipse cx="20" cy="8" rx="14" ry="5" fill="#888"/><path d="M6 8V30C6 33 12 35 20 35S34 33 34 30V8" fill="none" stroke="#888" stroke-width="3"/><path d="M6 19C6 22 12 24 20 24S34 22 34 19" fill="none" stroke="#888" stroke-width="3"/></svg>
  <div class="abs section-no" style="top:2512px">04</div>
  <div class="abs side-dots" style="top:2550px"><span></span><span></span><span></span><span class="on"></span><span></span><span></span></div>
  <p class="abs resources-text">Lorem ipsum dolor sit amet, consectetur adipiscing elit, sed do eiusmod tempor incididunt ut labore et dolore magna aliqua. Ut enim ad minim veniam, quis nostrud exercitation ullamco laboris nisi ut aliquip ex ea commodo consequat. Duis aute irure dolor in reprehenderit in voluptate velit esse cillum dolore eu fugiat nulla pariatur.</p>
  <a class="abs btn res-btn" href="#">READ MORE</a>

  <!-- Blog -->
  <h2 class="abs section-title" style="top:2880px">Our Blog</h2>
  <svg class="abs section-icon" style="top:2955px" width="40" height="44" viewBox="0 0 40 44"><rect x="8" y="2" width="26" height="34" fill="none" stroke="#888" stroke-width="3"/><rect x="3" y="8" width="26" height="34" fill="#fff" stroke="#888" stroke-width="3"/><line x1="9" y1="18" x2="23" y2="18" stroke="#888" stroke-width="2"/><line x1="9" y1="25" x2="23" y2="25" stroke="#888" stroke-width="2"/></svg>
  <div class="abs section-no" style="top:3030px">05</div>
  <div class="abs side-dots" style="top:3068px"><span></span><span></span><span></span><span></span><span class="on"></span><span></span></div>

  <article class="post" style="left:110px">
    <div class="post-img" role="img" aria-label="Person walking down a data centre aisle" style="background:linear-gradient(160deg,#3a3e44,#8b9097 50%,#d7d9dc)"></div>
    <p>Lorem ipsum dolor sit amet, consectetur adipiscing elit, sed do eiusmod tempor incididunt ut</p>
    <div class="post-meta"><span class="author"><i></i>MARCUS BELL</span><a class="btn" href="#">View Details</a></div>
  </article>
  <article class="post" style="left:450px">
    <div class="post-img" role="img" aria-label="Hands using a smartphone beside a laptop" style="background:linear-gradient(160deg,#7fa3c4,#c8d6e3 55%,#eef2f6)"></div>
    <p>Lorem ipsum dolor sit amet, consectetur adipiscing elit, sed do eiusmod tempor incididunt ut</p>
    <div class="post-meta"><span class="author"><i></i>MARCUS BELL</span><a class="btn" href="#">View Details</a></div>
  </article>
  <article class="post" style="left:790px">
    <div class="post-img" role="img" aria-label="Glowing network connections on a dark background" style="background:radial-gradient(circle at 55% 45%,#3c7ea8,#0e2a44 60%,#06131f)"></div>
    <p>Lorem ipsum dolor sit amet, consectetur adipiscing elit, sed do eiusmod tempor incididunt ut</p>
    <div class="post-meta"><span class="author"><i></i>MARCUS BELL</span><a class="btn" href="#">View Details</a></div>
  </article>

  <!-- Footer -->
  <svg class="abs" style="left:0;top:3470px" width="1200" height="610" viewBox="0 0 1200 610"><path d="M1200 0C1030 20 900 100 760 140 640 175 600 300 630 420 650 520 640 580 600 610H1200Z" fill="var(--red)"/></svg>
  <div class="abs brand footer-brand"><span class="brand-mark"></span><span class="brand-name">Vaultmerrow</span></div>
  <div class="abs section-no" style="top:3740px">06</div>
  <div class="abs side-dots" style="top:3778px"><span></span><span></span><span></span><span></span><span></span><span class="on"></span></div>

  <div class="abs foot-col" style="left:150px">
    <h3 class="foot-title">Contact Us</h3>
    <dl><dt>Email address</dt><dd>info@vaultmerrow.com.au</dd><dt>Call us</dt><dd>+61 2 5550 0147</dd></dl>
    <div class="socials"><span></span><span></span><span></span><span></span><span></span><span></span></div>
  </div>
  <div class="abs foot-col" style="left:400px">
    <h3 class="foot-title">Links</h3>
    <ul class="links"><li>Services</li><li>About</li><li>Resources</li><li>Blog</li><li>Contact Us</li></ul>
  </div>
  <div class="abs newsletter">
    <h3>Newsletter</h3>
    <p>Lorem ipsum dolor sit amet, consectetur adipiscing elit, sed do eiusmod tempor incididunt ut</p>
    <div class="signup"><span>Enter Your Email Address</span><b>Sign Up</b></div>
  </div>
  <div class="abs copyright">© Copyright 2019 The Company name All Rights Reserved</div>
</div>
</body>
</html>
```